I am looking for a poster design with a pledge for my clients to take. The pledge will be to not use tanning beds. Our company is a Spray Tanning Salon that focuses on educating our clients on the dangers of indoor tanning while offering a safe alternative through spray tanning. I have an outline of a possible wording but I am VERY open to adjustments on it!
This is not a promotional poster. This is a poster that will be hanging in the salon and our clients will sign around the wall.
Updates

Project Deadline Extended Reason: Not currently in love with any submissions and would like to see more. Looking for a more simple design overall. Added Friday, October 28, 2016

Target Market(s)

Women 20-30 years old

Industry/Entity Type

Salon

Font styles to use
Sans Serif

Requirements
Must have
• Take the pledge to ditch the bed!
• Maple Hollow Tanning
• **Overall simple design, yet eye catching is requested. Not so busy**
Nice to have
• I am open to different wording!
• I pledge to be timeless
• -UVA rays in tanning beds cause wrinkles and other signs of premature aging
• I pledge to be fearless
• -Using tanning beds can cause severe eye damage, a weakened immune system, and melanoma the deadliest form of skin cancer.
• I pledge to be Sunless!
• -Join the GlowWell revolution at Maple Hollow Tanning, Grand Rapids first Sunless Spa Experience.
Should not have
• The photo of the salon on it. I included that photo simply for reference of design, this is where this poster will be hung.

```html
<!DOCTYPE html>
<html lang="en">
<head>
<meta charset="utf-8">
<title>Maple Hollow Tanning Pledge Poster</title>
<link rel="stylesheet" href="https://fonts.googleapis.com/css2?family=Poiret+One&display=swap">
<style>
  :root {
    --backdrop: #f3f3f1;
    --berry: #cf2a62;
    --leaf: #6a9140;
    --night: #141312;
    --skin-glow: #6b5a4c;
    --white: #ffffff;
  }
  html, body {
    margin: 0;
    padding: 0;
    width: 1200px;
    height: 910px;
    overflow: hidden;
    background: var(--backdrop);
  }
  .poster {
    position: absolute;
    left: 278px;
    top: 0;
    width: 644px;
    height: 910px;
    overflow: hidden;
    background: var(--night);
    font-family: "Poiret One", sans-serif;
    color: var(--white);
  }
  .poster-photo {
    position: absolute;
    inset: 0;
    background:
      radial-gradient(ellipse 45% 70% at 62% 45%, var(--skin-glow) 0%, rgba(80,66,56,0.55) 40%, rgba(20,19,18,0) 75%),
      linear-gradient(180deg, #2a2724 0%, #191816 55%, #0f0e0d 100%);
  }
  .poster-bands {
    position: absolute;
    inset: 0;
    width: 644px;
    height: 910px;
  }
  .band-top { fill: var(--berry); }
  .band-bottom { fill: var(--leaf); }
  .band-edge { fill: none; stroke: var(--white); stroke-width: 4; }
  .pledge-headline {
    position: absolute;
    left: 0;
    right: 0;
    top: 18px;
    margin: 0;
    text-align: center;
    font-size: 27px;
    font-weight: 400;
    letter-spacing: 1px;
    line-height: 1;
  }
  .brand {
    position: absolute;
    left: 72px;
    top: 438px;
    width: 500px;
    line-height: 1;
  }
  .brand-name {
    margin: 0;
    font-size: 68px;
    font-weight: 400;
    letter-spacing: 1px;
    white-space: nowrap;
  }
  .brand-sub {
    margin: 10px 0 0;
    padding-left: 168px;
    font-size: 46px;
    letter-spacing: 2px;
  }
  .pledge-list {
    position: absolute;
    left: 0;
    right: 0;
    top: 852px;
    margin: 0;
    text-align: center;
    font-size: 22px;
    letter-spacing: 1px;
    line-height: 1;
    white-space: nowrap;
  }
</style>
</head>
<body>
  <main class="poster">
    <div class="poster-photo" role="img" aria-label="Photograph of a woman in a bikini behind a wet glass pane, dark moody background"></div>
    <svg class="poster-bands" viewBox="0 0 644 910" aria-hidden="true">
      <path class="band-top" d="M0 0 H644 V128 C560 150 470 120 360 100 C260 82 200 60 150 72 C90 86 40 120 0 168 Z"/>
      <path class="band-edge" d="M0 168 C40 120 90 86 150 72 C200 60 260 82 360 100 C470 120 560 150 644 128"/>
      <path class="band-bottom" d="M0 790 C120 760 260 775 380 815 C470 845 560 830 644 758 V910 H0 Z"/>
      <path class="band-edge" d="M0 790 C120 760 260 775 380 815 C470 845 560 830 644 758"/>
    </svg>
    <h2 class="pledge-headline">TAKE THE PLEDGE TO DITCH THE BED!</h2>
    <header class="brand">
      <h1 class="brand-name">MAPLE HOLLOW</h1>
      <p class="brand-sub">TANNING</p>
    </header>
    <p class="pledge-list">I PLEDGE TO BE TIMELESS · FEARLESS · SUNLESS</p>
  </main>
</body>
</html>
```